Packaging design for a reclosable bag for our product

We have a logo, and we need to put it on packaging for our product and while we want the look to be simple, we want it to follow good design principles and also contain spaces for other product descriptions.

There will be 5 sizes at launch so I'd like 5 variations, one for each size.

I've included a few mockups of the type of bag that I made but they are all just rough ideas that I had.

I want the brand to look scientific and methodical and even a bit quirky, as in "wow this is a serious product but also a bit unusual."

```html
<!DOCTYPE html>
<html lang="en">
<head>
<meta charset="UTF-8">
<title>Bias Lighting – Extra Large Pouch</title>
<link href="https://fonts.googleapis.com/css2?family=Barlow:wght@500;600&family=Barlow+Condensed:wght@500;600;700&display=swap" rel="stylesheet">
<style>
  :root {
    --backdrop: #2f3034;
    --pouch: #0c0c0d;
    --ink: #f4f4f4;
    --ink-soft: #d9d9d9;
    --band-light: #5a5a5c;
    --band-dark: #161617;
    --pill-grey: #6b6b6d;
  }
  * { margin: 0; padding: 0; box-sizing: border-box; }
  html, body {
    width: 1200px; height: 833px; overflow: hidden;
    background: var(--backdrop);
  }
  .pouch-front {
    position: absolute;
    left: 350px; top: 66px;
    width: 500px; height: 700px;
    background: var(--pouch);
    overflow: hidden;
  }
  .pouch-bands { position: absolute; inset: 0; }
  .size-badge {
    position: absolute; left: 54px; top: 80px;
    width: 62px; height: 62px; border-radius: 50%;
    background: var(--ink); color: #111;
    display: flex; flex-direction: column; align-items: center; justify-content: center;
    font-family: "Barlow Condensed", sans-serif;
  }
  .size-badge__value { font-size: 24px; font-weight: 700; line-height: 0.9; }
  .size-badge__unit { font-size: 9px; font-weight: 600; letter-spacing: 0.3px; }
  .category-title {
    position: absolute; left: 116px; top: 190px; width: 290px;
    font-family: "Barlow", sans-serif; font-weight: 600;
    font-size: 31px; letter-spacing: 4.6px; color: var(--ink);
    white-space: nowrap;
  }
  .size-pill {
    position: absolute; left: 121px; top: 225px;
    width: 270px; height: 22px; border-radius: 11px;
    background: var(--ink); color: #222;
    font-family: "Barlow", sans-serif; font-weight: 500;
    font-size: 11px; letter-spacing: 7px;
    display: flex; align-items: center; justify-content: center;
    padding-left: 7px;
  }
  .product-name {
    position: absolute; left: 96px; top: 246px; width: 320px;
    font-family: "Barlow", sans-serif; font-weight: 600;
    font-size: 228px; line-height: 1; letter-spacing: -8px;
    color: var(--ink); text-align: center;
  }
  .spec-pill {
    position: absolute; left: 122px; top: 478px;
    width: 255px; height: 38px; border-radius: 19px;
    background: linear-gradient(90deg, var(--pill-grey) 0%, #3a3a3c 45%, var(--pouch) 100%);
    display: flex; align-items: center; gap: 7px; padding-left: 12px;
    font-family: "Barlow Condensed", sans-serif; font-weight: 700;
    font-size: 21px; color: var(--ink); white-space: nowrap;
  }
  .spec-pill svg { width: 18px; height: 18px; }
  .colour-temp {
    position: absolute; left: 330px; top: 590px;
    font-family: "Barlow Condensed", sans-serif; color: var(--ink);
    text-align: left;
  }
  .colour-temp__value { font-size: 32px; font-weight: 700; line-height: 1; }
  .colour-temp__label { font-size: 9.5px; font-weight: 500; color: var(--ink-soft); letter-spacing: 0.1px; }
</style>
</head>
<body>
  <main class="pouch-front">
    <svg class="pouch-bands" viewBox="0 0 500 700" role="img" aria-label="Fine curved line pattern bands in grey across the top and bottom of the pouch">
      <defs>
        <linearGradient id="bandTop" x1="0" y1="0" x2="1" y2="1">
          <stop offset="0" stop-color="var(--band-dark)"/>
          <stop offset="0.45" stop-color="var(--band-light)"/>
          <stop offset="1" stop-color="var(--band-dark)"/>
        </linearGradient>
        <linearGradient id="bandBottom" x1="0" y1="1" x2="1" y2="0">
          <stop offset="0" stop-color="var(--band-light)"/>
          <stop offset="0.6" stop-color="#2a2a2b"/>
          <stop offset="1" stop-color="var(--band-dark)"/>
        </linearGradient>
      </defs>
      <path d="M0 0 H500 V42 C330 40 130 95 0 200 Z" fill="url(#bandTop)" opacity="0.55"/>
      <path d="M0 700 V600 C140 570 320 520 500 450 V700 Z" fill="url(#bandBottom)" opacity="0.6"/>
      <path d="M0 640 C160 610 330 560 500 510" fill="none" stroke="#000" stroke-width="26" opacity="0.7"/>
    </svg>

    <div class="size-badge">
      <span class="size-badge__value">5</span>
      <span class="size-badge__unit">METERS</span>
    </div>

    <h1 class="category-title">BIAS LIGHTING</h1>
    <div class="size-pill">EXTRA LARGUE</div>

    <div class="product-name">NV3</div>

    <div class="spec-pill">
      <svg viewBox="0 0 20 20" aria-hidden="true">
        <circle cx="10" cy="10" r="3.6" fill="none" stroke="#f4f4f4" stroke-width="1.4"/>
        <g stroke="#f4f4f4" stroke-width="1.4" stroke-linecap="round">
          <line x1="10" y1="1.5" x2="10" y2="3.5"/><line x1="10" y1="16.5" x2="10" y2="18.5"/>
          <line x1="1.5" y1="10" x2="3.5" y2="10"/><line x1="16.5" y1="10" x2="18.5" y2="10"/>
          <line x1="4" y1="4" x2="5.4" y2="5.4"/><line x1="14.6" y1="14.6" x2="16" y2="16"/>
          <line x1="4" y1="16" x2="5.4" y2="14.6"/><line x1="14.6" y1="5.4" x2="16" y2="4"/>
        </g>
      </svg>
      SIMULATED D65 CRI 90+
    </div>

    <div class="colour-temp">
      <div class="colour-temp__value">6500K</div>
      <div class="colour-temp__label">WHITE BIAS LIGHTING</div>
    </div>
  </main>
</body>
</html>
```